BRV Early College and Career Program

Starting a new program initiative at Birchmont Valley School where students will have the opportunity to take college courses during their senior year of high school. Preferably add some pictures to reflect the career pathways we are offering (below) Some context to use for this flyer are:

Learn more about the career focused courses in…
• Education
• Computer & Information Science
• Technology & Engineering
• Health

Things to look forward to:
Experience college in high school
Finish college early
Save money on college tuition and fees
Advice on Career pathways

all classes fit into OPAL CREDIT BUNDLE

For more information contact

Gavin Purdy - ZT12 Alliances -WHVC
555.014.2291
Email: gpurdy@whvc-example.edu

Ms. Okafuji- Early College Coordinator
Email: dena.okafuji@birchmont-example.org
Room J215

I uploaded 5 or so photos that I would like to see incorporated in the design of the flier- using real students from our high school will give a more realistic approach- thanks, Added Monday, August 21, 2017

Target Market(s)

High school students who are currently in 10th grade (for recruitment) and only high school juniors and seniors are able to apply.

Industry/Entity Type

School

Colors

Designer to choose colors to be used in the design.

Requirements
Must have
• logos- some pictures reflecting the different career pathways and the contact information provided. Looking to also have this in a format that I can print on card stock paper not just full length page- ADD / USE photos attached to see which one fits the project better.
Nice to have
• suitable for high school students- attractive
Should not have
• Do not include any generic phone numbers.

```html
<!DOCTYPE html>
<html lang="en">
<head>
<meta charset="utf-8">
<title>BRV Early College and Career Program – Print Sheet</title>
<link href="https://fonts.googleapis.com/css2?family=PT+Sans:wght@400;700&family=PT+Sans+Narrow:wght@400;700&display=swap" rel="stylesheet">
<style>
  :root{
    --navy:#1c3a6a;
    --navy-deep:#162f58;
    --blue:#2f6fb3;
    --sky:#4a8fd6;
    --icon:#3d7cc6;
    --photo-a:#8a6a5a;
    --photo-b:#3a3030;
    --ink:#1c3a6a;
    --grey:#4a4f5a;
    --white:#ffffff;
    --sheet:#ffffff;
  }
  *{box-sizing:border-box;margin:0;padding:0}
  html,body{width:971px;height:1200px;overflow:hidden;background:var(--sheet)}
  .sheet{position:relative;width:971px;height:1200px}
  .flyer{position:absolute;width:400px;height:548px;overflow:hidden;background:var(--white);font-family:"PT Sans",sans-serif}
  .flyer--a{left:152px;top:73px}
  .flyer--b{left:553px;top:73px}
  .flyer--c{left:152px;top:640px}
  .flyer--d{left:553px;top:640px}
  .flyer__shapes{position:absolute;inset:0;width:400px;height:548px}
  .brand{position:absolute;top:24px;display:flex;align-items:center;gap:4px;color:var(--navy);font-weight:700;font-size:9.5px;line-height:1.05}
  .brand--school{left:192px;width:96px}
  .brand--college{left:294px;width:104px}
  .brand__mark{width:10px;height:10px;background:var(--navy);flex:none}
  .title{position:absolute;left:206px;top:88px;width:190px;color:var(--white);font-weight:700;font-size:15px;line-height:1.3;text-align:center}
  .subtitle{position:absolute;left:200px;top:158px;width:196px;color:var(--navy);font-weight:700;font-size:9.4px;line-height:1.45;text-align:center}
  .perks{position:absolute;left:13px;top:233px;color:var(--navy)}
  .perks__head{font-weight:700;font-size:9.4px;text-transform:uppercase;margin-bottom:2px}
  .perks__list{list-style:none;font-size:9.6px;color:var(--grey);line-height:15px}
  .perks__list li{display:flex;align-items:center;gap:5px}
  .perks__list li::before{content:"";width:7px;height:7px;border-radius:50%;background:var(--sky);flex:none}
  .path{position:absolute;color:var(--white);font-family:"PT Sans Narrow",sans-serif;font-weight:700;font-size:8.2px;text-align:center;line-height:1.1;text-transform:uppercase}
  .path--edu{left:30px;top:430px;width:80px}
  .path--cis{left:108px;top:400px;width:100px}
  .path--eng{left:210px;top:370px;width:80px}
  .path--health{left:310px;top:328px;width:74px}
  .contact-bar{position:absolute;left:242px;top:446px;width:158px;height:16px;color:var(--white);font-family:"PT Sans Narrow",sans-serif;font-weight:700;font-size:8.2px;line-height:16px;text-align:center;text-transform:uppercase}
  .contacts{position:absolute;left:13px;top:490px;right:4px;display:flex;color:var(--white);font-size:6.8px;line-height:11px}
  .contact{flex:none}
  .contact--a{width:121px}
  .contact--b{width:128px}
  .contact__name{font-weight:700;font-size:8px}
  .contact__mail{display:flex;align-items:center;gap:3px}
  .contact__mail::before{content:"";width:7px;height:5px;background:var(--sky);flex:none}
</style>
</head>
<body>
<main class="sheet">

<!-- flyer template repeated four-up for card stock printing -->
<section class="flyer flyer--a">
  <svg class="flyer__shapes" viewBox="0 0 400 548" aria-hidden="false">
    <defs>
      <linearGradient id="photoTone" x1="0" y1="0" x2="1" y2="1">
        <stop offset="0" stop-color="#b89a86"/><stop offset="1" stop-color="#2e2a30"/>
      </linearGradient>
    </defs>
    <polygon points="0,0 140,0 200,95 200,217 0,217" fill="url(#photoTone)" role="img" aria-label="Photo of two students standing beside a video camera"/>
    <polygon points="140,0 152,0 212,95 200,95" fill="var(--blue)"/>
    <rect x="200" y="82" width="200" height="68" fill="var(--navy)"/>
    <polygon points="0,352 400,246 400,262 0,368" fill="var(--sky)"/>
    <polygon points="0,368 400,262 400,548 0,548" fill="var(--navy)"/>
    <polygon points="0,368 400,262 400,280 0,386" fill="var(--navy-deep)"/>
    <g stroke="var(--white)" stroke-width="4" fill="var(--icon)">
      <circle cx="70" cy="386" r="35"/><circle cx="158" cy="355" r="33"/>
      <circle cx="244" cy="326" r="33"/><circle cx="347" cy="281" r="37"/>
    </g>
    <g fill="var(--white)">
      <polygon points="50,382 70,372 90,382 70,392"/><rect x="60" y="386" width="20" height="10"/><rect x="86" y="382" width="2" height="14"/>
      <rect x="146" y="346" width="24" height="16" rx="2" fill="none" stroke="var(--white)" stroke-width="2.5"/><rect x="140" y="364" width="36" height="3"/>
      <circle cx="244" cy="326" r="14"/><circle cx="244" cy="326" r="6" fill="var(--icon)"/>
      <g><rect x="241" y="308" width="6" height="36"/><rect x="226" y="323" width="36" height="6"/></g>
      <circle cx="244" cy="326" r="12"/><circle cx="244" cy="326" r="5" fill="var(--icon)"/>
      <rect x="343" y="260" width="8" height="42"/><rect x="331" y="274" width="32" height="8"/>
    </g>
    <polygon points="250,446 400,446 400,462 242,462" fill="var(--blue)"/>
    <rect x="0" y="538" width="400" height="10" fill="var(--sky)"/>
  </svg>
  <div class="brand brand--school"><span class="brand__mark"></span>Birchmont Public Schools</div>
  <div class="brand brand--college">Westhaven Valley Community College</div>
  <h1 class="title">BRV Early College and Career Program</h1>
  <p class="subtitle">Take career focused courses at Westhaven Valley and earn credit for both college and high school</p>
  <div class="perks">
    <h2 class="perks__head">Experience college while in high school :</h2>
    <ul class="perks__list"><li>Experience college while in high school</li><li>Finish college early</li><li>Save money on college tuition and fees</li><li>Get advice on your future career</li></ul>
  </div>
  <span class="path path--edu">Education</span>
  <span class="path path--cis">Computer &amp;<br>Information Science</span>
  <span class="path path--eng">Engineering</span>
  <span class="path path--health">Health</span>
  <div class="contact-bar">For more information contact</div>
  <div class="contacts">
    <div class="contact contact--a"><div class="contact__name">Marisol Quintero</div><div>Room J215</div><div class="contact__mail">mquintero@whvc-example.edu</div></div>
    <div class="contact contact--b"><div class="contact__name">Ms. Okafuji</div><div>Early College Coordinator</div><div>Room J215</div><div class="contact__mail">dena.okafuji@birchmont-example.org</div></div>
    <div class="contact"><div class="contact__name">Ms. Valdane</div><div>Work-Based Learning Coordinator</div><div>Room J215</div><div class="contact__mail">r.valdane@birchmont-example.org</div></div>
  </div>
</section>

<section class="flyer flyer--b">
  <svg class="flyer__shapes" viewBox="0 0 400 548">
    <polygon points="0,0 140,0 200,95 200,217 0,217" fill="url(#photoTone)" role="img" aria-label="Photo of two students standing beside a video camera"/>
    <polygon points="140,0 152,0 212,95 200,95" fill="var(--blue)"/>
    <rect x="200" y="82" width="200" height="68" fill="var(--navy)"/>
    <polygon points="0,352 400,246 400,262 0,368" fill="var(--sky)"/>
    <polygon points="0,368 400,262 400,548 0,548" fill="var(--navy)"/>
    <polygon points="0,368 400,262 400,280 0,386" fill="var(--navy-deep)"/>
    <g stroke="var(--white)" stroke-width="4" fill="var(--icon)">
      <circle cx="70" cy="386" r="35"/><circle cx="158" cy="355" r="33"/>
      <circle cx="244" cy="326" r="33"/><circle cx="347" cy="281" r="37"/>
    </g>
    <g fill="var(--white)">
      <polygon points="50,382 70,372 90,382 70,392"/><rect x="60" y="386" width="20" height="10"/><rect x="86" y="382" width="2" height="14"/>
      <rect x="146" y="346" width="24" height="16" rx="2" fill="none" stroke="var(--white)" stroke-width="2.5"/><rect x="140" y="364" width="36" height="3"/>
      <rect x="241" y="308" width="6" height="36"/><rect x="226" y="323" width="36" height="6"/>
      <circle cx="244" cy="326" r="12"/><circle cx="244" cy="326" r="5" fill="var(--icon)"/>
      <rect x="343" y="260" width="8" height="42"/><rect x="331" y="274" width="32" height="8"/>
    </g>
    <polygon points="250,446 400,446 400,462 242,462" fill="var(--blue)"/>
    <rect x="0" y="538" width="400" height="10" fill="var(--sky)"/>
  </svg>
  <div class="brand brand--school"><span class="brand__mark"></span>Birchmont Public Schools</div>
  <div class="brand brand--college">Westhaven Valley Community College</div>
  <h1 class="title">BRV Early College and Career Program</h1>
  <p class="subtitle">Take career focused courses at Westhaven Valley and earn credit for both college and high school</p>
  <div class="perks">
    <h2 class="perks__head">Experience college while in high school :</h2>
    <ul class="perks__list"><li>Experience college while in high school</li><li>Finish college early</li><li>Save money on college tuition and fees</li><li>Get advice on your future career</li></ul>
  </div>
  <span class="path path--edu">Education</span>
  <span class="path path--cis">Computer &amp;<br>Information Science</span>
  <span class="path path--eng">Engineering</span>
  <span class="path path--health">Health</span>
  <div class="contact-bar">For more information contact</div>
  <div class="contacts">
    <div class="contact contact--a"><div class="contact__name">Marisol Quintero</div><div>Room J215</div><div class="contact__mail">mquintero@whvc-example.edu</div></div>
    <div class="contact contact--b"><div class="contact__name">Ms. Okafuji</div><div>Early College Coordinator</div><div>Room J215</div><div class="contact__mail">dena.okafuji@birchmont-example.org</div></div>
    <div class="contact"><div class="contact__name">Ms. Valdane</div><div>Work-Based Learning Coordinator</div><div>Room J215</div><div class="contact__mail">r.valdane@birchmont-example.org</div></div>
  </div>
</section>

<section class="flyer flyer--c">
  <svg class="flyer__shapes" viewBox="0 0 400 548">
    <polygon points="0,0 140,0 200,95 200,217 0,217" fill="url(#photoTone)" role="img" aria-label="Photo of two students standing beside a video camera"/>
    <polygon points="140,0 152,0 212,95 200,95" fill="var(--blue)"/>
    <rect x="200" y="82" width="200" height="68" fill="var(--navy)"/>
    <polygon points="0,352 400,246 400,262 0,368" fill="var(--sky)"/>
    <polygon points="0,368 400,262 400,548 0,548" fill="var(--navy)"/>
    <polygon points="0,368 400,262 400,280 0,386" fill="var(--navy-deep)"/>
    <g stroke="var(--white)" stroke-width="4" fill="var(--icon)">
      <circle cx="70" cy="386" r="35"/><circle cx="158" cy="355" r="33"/>
      <circle cx="244" cy="326" r="33"/><circle cx="347" cy="281" r="37"/>
    </g>
    <g fill="var(--white)">
      <polygon points="50,382 70,372 90,382 70,392"/><rect x="60" y="386" width="20" height="10"/><rect x="86" y="382" width="2" height="14"/>
      <rect x="146" y="346" width="24" height="16" rx="2" fill="none" stroke="var(--white)" stroke-width="2.5"/><rect x="140" y="364" width="36" height="3"/>
      <rect x="241" y="308" width="6" height="36"/><rect x="226" y="323" width="36" height="6"/>
      <circle cx="244" cy="326" r="12"/><circle cx="244" cy="326" r="5" fill="var(--icon)"/>
      <rect x="343" y="260" width="8" height="42"/><rect x="331" y="274" width="32" height="8"/>
    </g>
    <polygon points="250,446 400,446 400,462 242,462" fill="var(--blue)"/>
    <rect x="0" y="538" width="400" height="10" fill="var(--sky)"/>
  </svg>
  <div class="brand brand--school"><span class="brand__mark"></span>Birchmont Public Schools</div>
  <div class="brand brand--college">Westhaven Valley Community College</div>
  <h1 class="title">BRV Early College and Career Program</h1>
  <p class="subtitle">Take career focused courses at Westhaven Valley and earn credit for both college and high school</p>
  <div class="perks">
    <h2 class="perks__head">Experience college while in high school :</h2>
    <ul class="perks__list"><li>Experience college while in high school</li><li>Finish college early</li><li>Save money on college tuition and fees</li><li>Get advice on your future career</li></ul>
  </div>
  <span class="path path--edu">Education</span>
  <span class="path path--cis">Computer &amp;<br>Information Science</span>
  <span class="path path--eng">Engineering</span>
  <span class="path path--health">Health</span>
  <div class="contact-bar">For more information contact</div>
  <div class="contacts">
    <div class="contact contact--a"><div class="contact__name">Marisol Quintero</div><div>Room J215</div><div class="contact__mail">mquintero@whvc-example.edu</div></div>
    <div class="contact contact--b"><div class="contact__name">Ms. Okafuji</div><div>Early College Coordinator</div><div>Room J215</div><div class="contact__mail">dena.okafuji@birchmont-example.org</div></div>
    <div class="contact"><div class="contact__name">Ms. Valdane</div><div>Work-Based Learning Coordinator</div><div>Room J215</div><div class="contact__mail">r.valdane@birchmont-example.org</div></div>
  </div>
</section>

<section class="flyer flyer--d">
  <svg class="flyer__shapes" viewBox="0 0 400 548">
    <polygon points="0,0 140,0 200,95 200,217 0,217" fill="url(#photoTone)" role="img" aria-label="Photo of two students standing beside a video camera"/>
    <polygon points="140,0 152,0 212,95 200,95" fill="var(--blue)"/>
    <rect x="200" y="82" width="200" height="68" fill="var(--navy)"/>
    <polygon points="0,352 400,246 400,262 0,368" fill="var(--sky)"/>
    <polygon points="0,368 400,262 400,548 0,548" fill="var(--navy)"/>
    <polygon points="0,368 400,262 400,280 0,386" fill="var(--navy-deep)"/>
    <g stroke="var(--white)" stroke-width="4" fill="var(--icon)">
      <circle cx="70" cy="386" r="35"/><circle cx="158" cy="355" r="33"/>
      <circle cx="244" cy="326" r="33"/><circle cx="347" cy="281" r="37"/>
    </g>
    <g fill="var(--white)">
      <polygon points="50,382 70,372 90,382 70,392"/><rect x="60" y="386" width="20" height="10"/><rect x="86" y="382" width="2" height="14"/>
      <rect x="146" y="346" width="24" height="16" rx="2" fill="none" stroke="var(--white)" stroke-width="2.5"/><rect x="140" y="364" width="36" height="3"/>
      <rect x="241" y="308" width="6" height="36"/><rect x="226" y="323" width="36" height="6"/>
      <circle cx="244" cy="326" r="12"/><circle cx="244" cy="326" r="5" fill="var(--icon)"/>
      <rect x="343" y="260" width="8" height="42"/><rect x="331" y="274" width="32" height="8"/>
    </g>
    <polygon points="250,446 400,446 400,462 242,462" fill="var(--blue)"/>
    <rect x="0" y="538" width="400" height="10" fill="var(--sky)"/>
  </svg>
  <div class="brand brand--school"><span class="brand__mark"></span>Birchmont Public Schools</div>
  <div class="brand brand--college">Westhaven Valley Community College</div>
  <h1 class="title">BRV Early College and Career Program</h1>
  <p class="subtitle">Take career focused courses at Westhaven Valley and earn credit for both college and high school</p>
  <div class="perks">
    <h2 class="perks__head">Experience college while in high school :</h2>
    <ul class="perks__list"><li>Experience college while in high school</li><li>Finish college early</li><li>Save money on college tuition and fees</li><li>Get advice on your future career</li></ul>
  </div>
  <span class="path path--edu">Education</span>
  <span class="path path--cis">Computer &amp;<br>Information Science</span>
  <span class="path path--eng">Engineering</span>
  <span class="path path--health">Health</span>
  <div class="contact-bar">For more information contact</div>
  <div class="contacts">
    <div class="contact contact--a"><div class="contact__name">Marisol Quintero</div><div>Room J215</div><div class="contact__mail">mquintero@whvc-example.edu</div></div>
    <div class="contact contact--b"><div class="contact__name">Ms. Okafuji</div><div>Early College Coordinator</div><div>Room J215</div><div class="contact__mail">dena.okafuji@birchmont-example.org</div></div>
    <div class="contact"><div class="contact__name">Ms. Valdane</div><div>Work-Based Learning Coordinator</div><div>Room J215</div><div class="contact__mail">r.valdane@birchmont-example.org</div></div>
  </div>
</section>

</main>
</body>
</html>
```